Coastline Premier Retreats Business Card Design

Design a business card for Coastline Premier Retreats. Look at the website for colors and reference. Card should have logo, name, title, office number, mobile number, email, URL and a tagline like, "Luxury Hotel & Resort Email Marketing" (This might change).

https://www.coastlinepremierretreats.example

The rest I will leave up to your imagination.

Contact Information for Business Card

Logo, name, title, office number, mobile number, email, URL and a tagline like, "Luxury Hotel & Resort Email Marketing" (This might change).

```html
<!DOCTYPE html>
<html lang="en">
<head>
<meta charset="utf-8">
<title>Coastline Premier Retreats – Business Card</title>
<link href="https://fonts.googleapis.com/css2?family=Arimo:wght@400;700&display=swap" rel="stylesheet">
<style>
  :root {
    --stage: #2a2a2a;
    --card: #1b1b1b;
    --card-back: #161616;
    --accent: #f07a1a;
    --ink: #ffffff;
    --ink-soft: #e6e6e6;
    --emboss: #2b2b2b;
  }
  * { box-sizing: border-box; margin: 0; padding: 0; }
  html, body {
    width: 1200px; height: 915px; overflow: hidden;
    background: var(--stage);
    font-family: "Arimo", Arial, sans-serif;
  }
  .stage {
    position: relative; width: 1200px; height: 915px;
  }
  .card {
    position: absolute; left: 300px;
    width: 600px; height: 343px;
    border-radius: 22px;
    box-shadow: 0 14px 30px rgba(0,0,0,.55);
  }
  .card--back { top: 70px; background: var(--card-back); }
  .card--front { top: 480px; background: var(--card); }

  /* back side: tone-on-tone brand name */
  .brand-back {
    position: absolute; inset: 0;
    display: flex; align-items: center; justify-content: center; gap: 14px;
  }
  .brand-back .brand-mark {
    width: 22px; height: 22px; background: var(--emboss);
  }
  .brand-back .brand-name {
    font-weight: 700; font-size: 34px; letter-spacing: 1px;
    color: var(--emboss); text-transform: uppercase;
  }

  /* front side */
  .brand-front {
    position: absolute; top: 58px; left: 0; right: 0;
    display: flex; align-items: center; justify-content: center; gap: 12px;
  }
  .brand-front .brand-mark {
    width: 18px; height: 18px; background: var(--accent);
  }
  .brand-front .brand-name {
    font-weight: 700; font-size: 26px; letter-spacing: .5px;
    color: var(--ink); text-transform: uppercase;
  }

  .details {
    position: absolute; top: 140px; left: 40px; right: 40px;
    display: flex; justify-content: center; align-items: stretch;
  }
  .person {
    text-align: right; padding-right: 22px;
  }
  .person-name {
    font-weight: 700; font-size: 25px; color: var(--accent);
    text-transform: uppercase; letter-spacing: .5px; line-height: 1.1;
  }
  .person-title {
    font-size: 15px; color: var(--ink-soft); margin-top: 4px;
  }
  .person-address {
    font-size: 14px; color: var(--ink-soft); line-height: 1.35; margin-top: 6px;
  }
  .divider {
    width: 1.5px; background: var(--accent);
  }
  .contacts {
    list-style: none; padding-left: 22px;
  }
  .contacts li {
    display: flex; align-items: center; gap: 9px;
    font-size: 14px; color: var(--ink-soft); line-height: 1.65;
  }
  .contacts svg { width: 12px; height: 12px; flex: none; }

  .tagline {
    position: absolute; bottom: 42px; left: 0; right: 0;
    text-align: center; font-size: 15px; color: var(--ink-soft);
  }
</style>
</head>
<body>
<main class="stage">

  <section class="card card--back" aria-label="Card back">
    <div class="brand-back">
      <span class="brand-mark"></span>
      <span class="brand-name">Coastline Premier Retreats</span>
    </div>
  </section>

  <section class="card card--front" aria-label="Card front">
    <div class="brand-front">
      <span class="brand-mark"></span>
      <span class="brand-name">Coastline Premier Retreats</span>
    </div>

    <div class="details">
      <div class="person">
        <p class="person-name">Marcus Delane</p>
        <p class="person-title">CEO/Founder</p>
        <p class="person-address">PO Box, 48 B Harbor Rd<br>North Coast, CA 90210</p>
      </div>
      <div class="divider"></div>
      <ul class="contacts">
        <li>
          <svg viewBox="0 0 12 12"><rect x="3" y="0.5" width="6" height="11" rx="1.2" fill="none" stroke="var(--accent)" stroke-width="1.2"/><circle cx="6" cy="9.6" r=".7" fill="var(--accent)"/></svg>
          555.014.2200
        </li>
        <li>
          <svg viewBox="0 0 12 12"><path d="M1 5c0-2 2-3 5-3s5 1 5 3l-2 .6-.6-1.6H3.6L3 5.6z" fill="var(--accent)"/><rect x="2.5" y="6.5" width="7" height="4" rx="1" fill="var(--accent)"/></svg>
          +34 600 000 412
        </li>
        <li>
          <svg viewBox="0 0 12 12"><rect x="0.8" y="2.5" width="10.4" height="7.5" rx="1" fill="none" stroke="var(--accent)" stroke-width="1.2"/><path d="M1 3l5 4 5-4" fill="none" stroke="var(--accent)" stroke-width="1.2"/></svg>
          info@coastlinepremierretreats.example
        </li>
        <li>
          <svg viewBox="0 0 12 12"><circle cx="6" cy="6" r="5" fill="none" stroke="var(--accent)" stroke-width="1.2"/><ellipse cx="6" cy="6" rx="2.2" ry="5" fill="none" stroke="var(--accent)" stroke-width="1"/><path d="M1 6h10" stroke="var(--accent)" stroke-width="1"/></svg>
          www.coastlinepremierretreats.example
        </li>
      </ul>
    </div>

    <p class="tagline">Luxury Hotel &amp; Resort Email Marketing</p>
  </section>

</main>
</body>
</html>
```